Health Care Company with Logo Needs Business Cards designed

We are a luxury behavioral health company looking for business cards design we already have a logo and are looking for someone to design a sophisticated luxurious looking business card. Please note that Card design should be captivating just like the logo and also encompass the logo color

Industry/Entity Type

Healthcare

Contact Information for Business Card

Logo,company name, tagline, my name and title, contact details, and physical address

```html
<!DOCTYPE html>
<html lang="en">
<head>
<meta charset="utf-8">
<title>Harlow Behavioral Health – Business Cards</title>
<link href="https://fonts.googleapis.com/css2?family=Roboto+Condensed:ital,wght@0,400;0,700;1,700&family=Roboto:wght@400&display=swap" rel="stylesheet">
<style>
  :root {
    --page: #2a2a2a;
    --card: #151515;
    --pattern-dark: #141414;
    --pattern-light: #262626;
    --blue: #1aa3e8;
    --orange: #f7941d;
    --green: #8cc63f;
    --purple: #7b3f9e;
    --ink: #f2f2f2;
  }
  * { margin: 0; padding: 0; box-sizing: border-box; }
  html, body { width: 1200px; height: 900px; overflow: hidden; background: var(--page); }
  .stage {
    width: 1200px; height: 900px;
    display: flex; flex-direction: column; align-items: center; justify-content: center; gap: 36px;
  }
  .card {
    position: relative; width: 700px; height: 400px; background: var(--card);
    font-family: "Roboto", Arial, sans-serif; color: var(--ink);
    box-shadow: 0 16px 40px rgba(0,0,0,.5);
    overflow: hidden;
  }

  /* Front */
  .brand { position: absolute; left: 44px; top: 112px; }
  .brand-name {
    display: flex; align-items: center; gap: 10px;
    font-family: "Roboto Condensed", Arial, sans-serif; font-weight: 700;
    font-size: 28px; color: var(--purple); letter-spacing: .3px; white-space: nowrap;
  }
  .brand-mark { width: 22px; height: 22px; background: var(--purple); flex: none; }
  .tagline {
    margin-top: 4px; margin-left: 32px;
    font-family: "Roboto Condensed", Arial, sans-serif; font-size: 10px;
    letter-spacing: 2.2px; color: var(--blue); text-transform: uppercase; white-space: nowrap;
  }
  .divider { position: absolute; left: 410px; top: 105px; width: 2px; height: 210px; background: var(--blue); }
  .contact { position: absolute; left: 432px; top: 112px; font-size: 16px; line-height: 1.35; white-space: nowrap; }
  .person-name {
    font-family: "Roboto Condensed", Arial, sans-serif; font-weight: 700; font-style: italic;
    font-size: 24px; line-height: 1.1; color: var(--blue); text-transform: uppercase; letter-spacing: .6px;
  }
  .person-title { font-size: 16px; margin-bottom: 14px; }
  .address { margin-bottom: 2px; }
  .line { display: flex; align-items: center; gap: 8px; font-size: 15px; }
  .line svg { width: 13px; height: 13px; flex: none; }
  .colour-bar { position: absolute; left: 0; bottom: 0; width: 100%; height: 9px; display: flex; }
  .colour-bar span { flex: 1; }
  .bar-blue { background: var(--blue); }
  .bar-orange { background: var(--orange); }
  .bar-green { background: var(--green); }
  .bar-purple { background: var(--purple); }

  /* Back */
  .back-pattern {
    position: absolute; inset: 0;
    background: linear-gradient(135deg, var(--pattern-light) 0%, var(--pattern-dark) 55%, var(--pattern-light) 100%);
  }
  .back-brand {
    position: absolute; right: 40px; bottom: 36px;
    display: flex; align-items: center; gap: 8px;
    font-family: "Roboto Condensed", Arial, sans-serif; font-weight: 700;
    font-size: 18px; color: var(--purple); white-space: nowrap;
  }
  .back-brand .brand-mark { width: 16px; height: 16px; }
</style>
</head>
<body>
<main class="stage">
  <section class="card card-front">
    <div class="brand">
      <div class="brand-name"><span class="brand-mark"></span>Harlow Behavioral Health</div>
      <p class="tagline">Dedicated to hope, healing and recovery</p>
    </div>

    <div class="divider"></div>

    <div class="contact">
      <p class="person-name">Daniel Reyes</p>
      <p class="person-title">President</p>
      <p class="address">1820 Harbor Crest Dr<br>Seaview CA 92600</p>
      <p class="line">
        <svg viewBox="0 0 20 20" aria-hidden="true"><path d="M5 2l3 4-2 2c1 2 3 4 5 5l2-2 4 3-2 3C9 17 3 11 2 4z" fill="var(--orange)"/></svg>
        555-310-4827
      </p>
      <p class="line">
        <svg viewBox="0 0 20 20" aria-hidden="true"><rect x="2" y="5" width="16" height="11" fill="var(--green)"/><path d="M2 5l8 6 8-6" fill="none" stroke="var(--card)" stroke-width="1.5"/></svg>
        info@harlowbehavioral.com
      </p>
      <p class="line">
        <svg viewBox="0 0 20 20" aria-hidden="true"><circle cx="10" cy="10" r="8" fill="var(--purple)"/><path d="M2 10h16M10 2c-3 3-3 13 0 16M10 2c3 3 3 13 0 16" fill="none" stroke="var(--card)" stroke-width="1.2"/></svg>
        www.harlowbehavioral.com
      </p>
    </div>

    <div class="colour-bar">
      <span class="bar-blue"></span><span class="bar-orange"></span><span class="bar-green"></span><span class="bar-purple"></span>
    </div>
  </section>

  <section class="card card-back">
    <div class="back-pattern" role="img" aria-label="Dark tone-on-tone repeating pattern of the brand symbol across the card back"></div>
    <div class="back-brand"><span class="brand-mark"></span>Harlow Behavioral Health</div>
  </section>
</main>
</body>
</html>
```